Business Card Design for ReaL ESTATE AGENT

New Business Cards for a real estate agent in Jacksonville, FL. My specialty is urban core, historic districts but sell through out the city. Company Name is Ninth and Crest Realty a division of the Dunholt Companies. The card needs to convey an essence of professionalism, knowledge and success.

Target Market(s)

Home buyers and Sellers

Industry/Entity Type

Real Estate

Contact Information for Business Card

Double sided

Font styles to use
Sans Serif

Requirements
Must have
• My logs and photo (provided). My contact information as follows:
• Owen Talbrick
• Cell 904-555-0183
• Office 904-555-0147
• Email owentalbrick@mailbrook.example
Nice to have
• Tag Line - Exceptional Effort. Proven Results.

```html
<!DOCTYPE html>
<html lang="en">
<head>
<meta charset="utf-8">
<title>Ninth and Crest Realty – Business Card</title>
<link rel="stylesheet" href="https://fonts.googleapis.com/css2?family=Source+Sans+3:wght@400;600;700&display=swap">
<style>
  :root {
    --backdrop: #9a9a9a;
    --card-white: #ffffff;
    --brand-green: #1e654b;
    --brand-coral: #ee8576;
    --brand-red: #e2533b;
    --text-light: #ffffff;
  }
  * { box-sizing: border-box; margin: 0; padding: 0; }
  html, body {
    width: 1200px;
    height: 900px;
    overflow: hidden;
  }
  body {
    background: var(--backdrop);
    font-family: "Source Sans 3", sans-serif;
    display: flex;
    flex-direction: column;
    align-items: center;
    justify-content: center;
    gap: 40px;
  }
  .card {
    position: relative;
    width: 700px;
    height: 400px;
    background: var(--card-white);
    overflow: hidden;
    box-shadow: 0 6px 18px rgba(0,0,0,0.25);
  }

  /* Front: brand side */
  .card-front {
    display: flex;
    align-items: center;
    justify-content: center;
  }
  .brand {
    display: flex;
    align-items: center;
    gap: 18px;
  }
  .brand-mark {
    width: 46px;
    height: 46px;
    background: var(--brand-green);
  }
  .brand-name {
    font-weight: 700;
    font-size: 40px;
    letter-spacing: 0.5px;
    color: var(--brand-red);
  }

  /* Back: agent side */
  .card-back .backdrop-shapes {
    position: absolute;
    inset: 0;
  }
  .agent-details {
    position: absolute;
    right: 36px;
    top: 120px;
    text-align: right;
    color: var(--text-light);
  }
  .agent-name {
    font-weight: 600;
    font-size: 27px;
    line-height: 1.1;
  }
  .agent-title {
    font-weight: 400;
    font-size: 18px;
    line-height: 1.4;
    margin-bottom: 14px;
  }
  .contact-line {
    display: flex;
    align-items: center;
    justify-content: flex-end;
    gap: 10px;
    font-size: 16px;
    line-height: 1.5;
  }
  .contact-icon {
    width: 13px;
    height: 13px;
    flex: none;
    fill: var(--text-light);
  }
</style>
</head>
<body>

  <section class="card card-front" aria-label="Business card front">
    <div class="brand">
      <div class="brand-mark"></div>
      <div class="brand-name">Ninth and Crest Realty</div>
    </div>
  </section>

  <section class="card card-back" aria-label="Business card back">
    <svg class="backdrop-shapes" width="700" height="400" viewBox="0 0 700 400">
      <defs>
        <linearGradient id="portraitTone" x1="0" y1="0" x2="0" y2="1">
          <stop offset="0" stop-color="#cfae98"/>
          <stop offset="0.45" stop-color="#a88876"/>
          <stop offset="1" stop-color="#3b3f45"/>
        </linearGradient>
      </defs>
      <rect class="agent-portrait" role="img" aria-label="Portrait photo of the agent"
            x="0" y="150" width="300" height="250" fill="url(#portraitTone)"/>
      <path class="accent-swoosh" fill="var(--brand-coral)"
            d="M352 0 C440 110 420 300 220 400 L252 400 C430 300 460 120 392 0 Z"/>
      <path class="green-panel" fill="var(--brand-green)"
            d="M400 0 C470 120 430 310 270 400 L700 400 L700 0 Z"/>
    </svg>

    <div class="agent-details">
      <div class="agent-name">Owen Talbrick</div>
      <div class="agent-title">Managing Director</div>
      <div class="contact-line">
        <span>Cell 904-555-0183</span>
        <svg class="contact-icon" viewBox="0 0 16 16" aria-hidden="true">
          <path d="M3 2h3l1.5 3.5-2 1.2a8 8 0 0 0 3.8 3.8l1.2-2L14 10v3a1 1 0 0 1-1 1A12 12 0 0 1 2 3a1 1 0 0 1 1-1z"/>
        </svg>
      </div>
      <div class="contact-line">
        <span>Office 904-555-0147</span>
        <svg class="contact-icon" viewBox="0 0 16 16" aria-hidden="true">
          <path d="M3 2h3l1.5 3.5-2 1.2a8 8 0 0 0 3.8 3.8l1.2-2L14 10v3a1 1 0 0 1-1 1A12 12 0 0 1 2 3a1 1 0 0 1 1-1z"/>
        </svg>
      </div>
      <div class="contact-line">
        <span>owentalbrick@mailbrook.example</span>
        <svg class="contact-icon" viewBox="0 0 16 16" aria-hidden="true">
          <path d="M1 3h14v10H1z M2 4l6 5 6-5" fill="none" stroke="#fff" stroke-width="1.5"/>
        </svg>
      </div>
    </div>
  </section>

</body>
</html>
```